R. Talmont Realty, Inc business card (2 sided), letterhead (1 sided) & #10 envelope (1 sided)

business card of standard size utilizing the attached logo. Side one with logo, Owen Talmont (my name), President / Broker (title), 805-317-2684 (phone), www.rtalmontrealty.example (website), 1726 Harlow Avenue, Suite 4052 San Luis Obiso, CA 93628 (business address) owen.rtalmontrealty@mailbox.example (e-mail address),
Side two - Log

Letterhead and #10 envelope in the same theme
Updates

Project Deadline Extended
Reason: I think a 2 day deadline may be a bit ambitious on my part. I have extended the deadline to 4 days. Thanks!

Industry/Entity Type

Business

```html
<!DOCTYPE html>
<html lang="en">
<head>
<meta charset="utf-8">
<title>R. Talmont Realty, Inc — Business Card</title>
<link rel="stylesheet" href="https://fonts.googleapis.com/css2?family=Bitter:wght@600;700&family=PT+Sans:wght@400&display=swap">
<style>
  :root {
    --backdrop: #ecebe8;
    --card-white: #ffffff;
    --brand-blue: #1d7fb0;
    --brand-blue-deep: #0f4f78;
    --brand-blue-light: #2a8fc4;
    --ink: #2b2b2b;
    --rule-dark: #2f3438;
    --charcoal: #3b3b3b;
    --on-dark: #ffffff;
  }
  * { box-sizing: border-box; margin: 0; padding: 0; }
  html, body {
    width: 1200px; height: 1182px; overflow: hidden;
    background: var(--backdrop);
  }
  .canvas { position: relative; width: 1200px; height: 1182px; }

  .card {
    position: absolute; width: 912px; height: 519px; overflow: hidden;
    box-shadow: 0 4px 14px rgba(0,0,0,.18);
  }

  /* Front side */
  .card--front { left: 256px; top: 42px; background: var(--card-white); }
  .brand {
    position: absolute; display: flex; align-items: center; gap: 14px;
    font-family: "Bitter", serif; font-weight: 700;
  }
  .card--front .brand { left: 44px; top: 120px; font-size: 38px; color: var(--brand-blue); }
  .brand__mark { width: 26px; height: 26px; background: currentColor; flex: none; }

  .holder { position: absolute; right: 34px; top: 66px; text-align: right; }
  .holder__name {
    font-family: "Bitter", serif; font-weight: 700; font-size: 32px;
    color: var(--brand-blue);
  }
  .holder__title {
    margin-top: 6px; font-family: "PT Sans", sans-serif; font-size: 27px;
    color: var(--ink);
  }

  .front__rule {
    position: absolute; left: 0; right: 0; top: 341px; height: 5px;
    background: var(--rule-dark);
  }
  .contact-band {
    position: absolute; left: 0; right: 0; top: 352px; bottom: 0;
    background: linear-gradient(90deg, var(--brand-blue-deep) 0%, var(--brand-blue) 55%, var(--brand-blue-light) 100%);
    padding: 20px 0 0 78px;
  }
  .contact-list { list-style: none; }
  .contact-list li {
    display: flex; align-items: center; gap: 10px; height: 47px;
    font-family: "PT Sans", sans-serif; font-size: 25px; color: var(--on-dark);
  }
  .contact-list svg { width: 20px; height: 20px; flex: none; }

  /* Back side */
  .card--back { left: 55px; top: 603px; background: var(--charcoal); }
  .card--back .brand {
    left: 0; right: 0; top: 170px; justify-content: center;
    font-size: 44px; color: var(--on-dark);
  }
  .card--back .brand__mark { width: 30px; height: 30px; }
  .back__web {
    position: absolute; left: 0; right: 0; top: 418px; text-align: center;
    font-family: "PT Sans", sans-serif; font-size: 27px; letter-spacing: 3px;
    color: var(--on-dark);
  }
</style>
</head>
<body>
<main class="canvas">

  <section class="card card--front" aria-label="Business card, front">
    <div class="brand"><span class="brand__mark"></span>R. Talmont Realty, Inc</div>

    <div class="holder">
      <p class="holder__name">Owen Talmont</p>
      <p class="holder__title">President / Broker</p>
    </div>

    <div class="front__rule"></div>

    <div class="contact-band">
      <ul class="contact-list">
        <li>
          <svg viewBox="0 0 20 20" aria-hidden="true"><path d="M5 2c1 0 2 3 2 4s-2 1-1 3 3 4 5 4 1-2 3-1 4 1 4 3-2 3-3 3C8 18 2 12 2 5 2 3 4 2 5 2z" fill="none" stroke="#fff" stroke-width="1.6"/></svg>
          805-317-2684
        </li>
        <li>
          <svg viewBox="0 0 20 20" aria-hidden="true"><path d="M2 8l8-5 8 5v9H2z" fill="#fff"/><path d="M2 8l8 5 8-5" fill="none" stroke="#1d6f9e" stroke-width="1.4"/></svg>
          owen.rtalmontrealty@mailbox.example
        </li>
        <li>
          <svg viewBox="0 0 20 20" aria-hidden="true" fill="none" stroke="#fff" stroke-width="1.4"><circle cx="10" cy="10" r="8"/><ellipse cx="10" cy="10" rx="3.5" ry="8"/><path d="M2 10h16M3.5 6h13M3.5 14h13"/></svg>
          www.rtalmontrealty.example
        </li>
      </ul>
    </div>
  </section>

  <section class="card card--back" aria-label="Business card, back">
    <div class="brand"><span class="brand__mark"></span>R. Talmont Realty, Inc</div>
    <p class="back__web">www.rtalmontrealty.example</p>
  </section>

</main>
</body>
</html>
```